Business Card: RW Office Partners - Your organised problem solver

Business Name: RW Office Partners
Website: www.rwofficepartners.com.au
Email: marisol@rwofficepartners.com.au
Mobile: 61 482 907 236
Facebook: @rwofficepartners
Instrgram: @rwofficepartners

Brading Colours:
HEX
#986474
#ddccd3
#7a8498
#c9d8e4
#000000
#ffffff

Tag Line: Your organised problem solver

Link to DRAFT website:
https://deskhelpcollective.wixsite.com/rw-office-partners

About Page from the website:
My name is Marisol Wrenfield, and I would love to assist you to become more productive in your day to day and achieve your business and personal goals.
My mission is to give you time, time to work on the important tasks of your business or to be able to spend more time with your family. I will take on the tasks you don’t have time for, don’t know well or simply don’t like to do.
I have an extensive background in Administration, Tender Coordination, Document Control, WHS and Quality Management working primarily in the Construction, Mining and Corporate World.
I am passionate about being organised, having order and making things in your life (and mine) easier! I love to watch something unfold and grow into something amazing! I am known for being the go-to problem solver, the organiser of all things, producing high standards of work even under pressure. I’m also a confident communicator, and I understand that you’re busy running your business.

Target Market(s)

Small to Medium Business who require assistance in their business by a virtual assistant.

Industry/Entity Type

Virtual Assistant

Contact Information for Business Card

Mobile: 61 482 907 236

Font styles to use
Sans Serif

Colors
ffffff

Requirements
Must have
• Branding Colours as outlined.
Contact Details as outlined.
Logo as provided.
Proper contact details - mobile, facebook, instragm, website.
Simple, Elegant, very clean looking.
Should not have
• Note cute with pictures.
Not too girly as still want to market to construction companies.

```html
<!DOCTYPE html>
<html lang="en">
<head>
<meta charset="utf-8">
<title>RW Office Partners – Business Card</title>
<link href="https://fonts.googleapis.com/css2?family=Roboto:wght@400;500;700&display=swap" rel="stylesheet">
<style>
  :root {
    --mauve: #986474;
    --mauve-deep: #835c6b;
    --slate: #7a8498;
    --ink: #3a3a3a;
    --paper: #ffffff;
    --backdrop: #6c6868;
    --rule: #8b8b8b;
  }
  * { margin: 0; padding: 0; box-sizing: border-box; }
  html, body { width: 1200px; height: 1200px; overflow: hidden; }
  body {
    background: var(--backdrop);
    font-family: "Roboto", Arial, sans-serif;
    color: var(--ink);
    position: relative;
  }
  .card {
    position: absolute;
    background: var(--paper);
    border-radius: 24px;
    overflow: hidden;
  }
  .card--front { left: 238px; top: 120px; width: 712px; height: 417px; }
  .card--back  { left: 231px; top: 645px; width: 711px; height: 416px; }

  .brand-name {
    position: absolute;
    left: 0; right: 0; top: 150px;
    text-align: center;
    font-weight: 500;
    font-size: 62px;
    letter-spacing: 0.5px;
    color: var(--mauve-deep);
  }

  .social {
    position: absolute;
    left: 0; right: 0;
    display: flex;
    justify-content: center;
    align-items: center;
    gap: 10px;
    font-size: 18px;
    color: var(--ink);
  }
  .social__item { display: flex; align-items: center; gap: 9px; }
  .social__mark {
    width: 15px; height: 15px;
    background: var(--mauve);
    border-radius: 3px;
  }
  .social__mark--round { border-radius: 50%; }
  .card--front .social { top: 350px; }

  .colour-band {
    position: absolute; left: 0; right: 0; bottom: 0; height: 16px;
    display: flex;
  }
  .colour-band__mauve { flex: 1; background: var(--mauve); }
  .colour-band__slate { flex: 1; background: var(--slate); }

  .monogram-name {
    position: absolute;
    left: 42px; top: 118px;
    width: 280px;
    font-weight: 500;
    font-size: 52px;
    line-height: 1.1;
    color: var(--mauve-deep);
  }

  .person { position: absolute; left: 354px; top: 112px; }
  .person__name {
    font-weight: 700; font-size: 25px; color: var(--mauve-deep);
  }
  .person__role { font-size: 18px; margin-top: 4px; color: var(--ink); }

  .contacts { position: absolute; left: 354px; top: 192px; list-style: none; }
  .contacts li {
    display: flex; align-items: center; gap: 13px;
    font-size: 19px; height: 26.5px;
  }
  .contacts svg { width: 18px; height: 18px; fill: var(--mauve); }

  .card--back .social { top: 366px; gap: 10px; }
  .social__rule { width: 92px; height: 1px; background: var(--rule); margin: 0 14px; }
</style>
</head>
<body>

<section class="card card--front" aria-label="Business card front">
  <div class="brand-name">RW Office Partners</div>
  <div class="social">
    <span class="social__item"><span class="social__mark"></span>@rwofficepartners</span>
    <span class="social__item"><span class="social__mark social__mark--round"></span>@rwofficepartners</span>
  </div>
  <div class="colour-band">
    <span class="colour-band__mauve"></span>
    <span class="colour-band__slate"></span>
  </div>
</section>

<section class="card card--back" aria-label="Business card back">
  <div class="monogram-name">RW Office Partners</div>

  <div class="person">
    <div class="person__name">Marisol Wrenfield</div>
    <div class="person__role">Virtual Assistant</div>
  </div>

  <ul class="contacts">
    <li>
      <svg viewBox="0 0 20 20" aria-hidden="true"><path d="M2 7c0-2 3-3 8-3s8 1 8 3v1h-4V6.5c-1-.4-2.5-.5-4-.5s-3 .1-4 .5V8H2zM5 9h10l2 7H3z"/></svg>
      61 482 907 236
    </li>
    <li>
      <svg viewBox="0 0 20 20" aria-hidden="true"><path d="M2 4h16v12H2zM3.5 5.5v.6L10 11l6.5-4.9v-.6zM3.5 8v6.5h13V8L10 13z"/></svg>
      marisol@rwofficepartners.com.au
    </li>
    <li>
      <svg viewBox="0 0 20 20" aria-hidden="true"><path d="M10 2a8 8 0 1 0 0 16 8 8 0 0 0 0-16zm0 1.5c.9 0 2 1.8 2.4 4.5H7.6C8 5.3 9.1 3.5 10 3.5zM3.6 9.3h2.6v1.4H3.6zm4 0h4.8v1.4H7.6zm6.2 0h2.6v1.4h-2.6zM7.6 12h4.8c-.4 2.7-1.5 4.5-2.4 4.5S8 14.7 7.6 12z"/></svg>
      www.rwofficepartners.com.au
    </li>
  </ul>

  <div class="social">
    <span class="social__rule"></span>
    <span class="social__item"><span class="social__mark"></span>@rwofficepartners</span>
    <span class="social__item"><span class="social__mark social__mark--round"></span>@rwofficepartners</span>
    <span class="social__rule"></span>
  </div>
</section>

</body>
</html>
```